Business card for Luxury Portable Restroom Trailer company

We are a Luxury Portable Restroom Trailer Company Called FALCRIDGE HIRES. Based in Orange County California. We provide portable restroom trailers for events, such as, Weddings, Concerts, Charity events, Sporting events, Tournaments, Corporate events, ect. We rent and Sell the Luxury restrooms. Our colors are white, grey, and Orange. As you will see in the logo we uploaded.
There are 2 people in the company so the names and titles will change for the 3 people but card will remain the same. Here is the information for each Person: Dwight Penner CFO 555 318-0476
next Person: Leon Marchetti VP 555 318-0476
Next Person: Owen Marchetti CEO 555 318-0476
Information to include on the card: Luxury Restroom Trailers Rental and Sales. Weddings, Concerts, Charity, Sporting and Corp. Events.

```html
<!DOCTYPE html>
<html lang="en">
<head>
<meta charset="utf-8">
<title>Falcridge Hires – Business Card</title>
<link rel="stylesheet" href="https://fonts.googleapis.com/css2?family=Montserrat:wght@400;500;700;800&display=swap">
<style>
  :root {
    --page: #2a2a2b;
    --card: #242425;
    --card-deep: #1d1d1e;
    --orange: #f26a1b;
    --white: #f4f4f4;
    --grey: #3a3a3c;
    --grey-light: #55565a;
  }
  * { margin: 0; padding: 0; box-sizing: border-box; }
  html, body { width: 1200px; height: 801px; overflow: hidden; }
  body {
    background: var(--page);
    font-family: "Montserrat", sans-serif;
    position: relative;
  }
  .card {
    position: absolute;
    top: 246px;
    width: 540px;
    height: 309px;
    background: linear-gradient(160deg, var(--card) 0%, var(--card-deep) 100%);
    border-bottom: 4px solid var(--orange);
    overflow: hidden;
  }
  .card--front { left: 40px; }
  .card--back { left: 620px; }

  /* front */
  .brand {
    position: absolute;
    left: 34px; top: 36px;
    display: flex; align-items: center; gap: 10px;
    color: var(--orange);
    font-weight: 800;
    font-size: 22px;
    letter-spacing: 0.5px;
  }
  .brand__square { width: 14px; height: 14px; background: var(--orange); }
  .person { position: absolute; left: 34px; top: 116px; }
  .person__name { color: var(--orange); font-weight: 800; font-size: 22px; letter-spacing: 1px; }
  .person__title { color: var(--white); font-weight: 400; font-size: 14px; margin-top: 2px; }
  .contacts { position: absolute; left: 34px; top: 196px; list-style: none; }
  .contacts li {
    display: flex; align-items: center; gap: 9px;
    color: var(--white); font-size: 13px; line-height: 24px;
  }
  .contacts svg { width: 12px; height: 12px; fill: var(--orange); }
  .emblem-ring {
    position: absolute; right: 36px; top: 46px;
    width: 200px; height: 200px; border-radius: 50%;
    border: 6px solid var(--grey);
    background: radial-gradient(circle at 40% 35%, #2c2c2e, var(--card-deep));
  }

  /* back */
  .back-brand {
    position: absolute; left: 0; right: 0; top: 92px;
    text-align: center;
    color: var(--grey-light);
    font-weight: 800; font-size: 40px; letter-spacing: 2px;
  }
  .tagline {
    position: absolute; left: 0; right: 0; top: 214px;
    text-align: center; color: var(--orange);
    font-weight: 500; font-size: 14px;
  }
  .events {
    position: absolute; left: 0; right: 0; top: 240px;
    text-align: center; color: var(--white);
    font-weight: 400; font-size: 14px;
  }
</style>
</head>
<body>
  <section class="card card--front">
    <div class="brand"><span class="brand__square"></span>FALCRIDGE HIRES</div>
    <div class="person">
      <div class="person__name">OWEN MARCHETTI</div>
      <div class="person__title">CEO</div>
    </div>
    <ul class="contacts">
      <li><svg viewBox="0 0 24 24"><path d="M6.6 10.8a15 15 0 0 0 6.6 6.6l2.2-2.2a1 1 0 0 1 1-.25 11.4 11.4 0 0 0 3.6.57 1 1 0 0 1 1 1V20a1 1 0 0 1-1 1A17 17 0 0 1 3 4a1 1 0 0 1 1-1h3.5a1 1 0 0 1 1 1c0 1.25.2 2.45.57 3.57a1 1 0 0 1-.25 1z"/></svg>555 318-0476</li>
      <li><svg viewBox="0 0 24 24"><path d="M2 5h20v14H2z M2 5l10 8 10-8" /></svg>owen@falcridgehires.com</li>
      <li><svg viewBox="0 0 24 24"><circle cx="12" cy="12" r="10"/></svg>www.falcridgehires.com</li>
    </ul>
    <div class="emblem-ring" role="img" aria-label="Large embossed brand emblem area"></div>
  </section>

  <section class="card card--back">
    <div class="back-brand">FALCRIDGE HIRES</div>
    <p class="tagline">Luxury Restroom Trailers Rental and Sales</p>
    <p class="events">Weddings | Concerts | Charity | Sporting | Corp</p>
  </section>
</body>
</html>
```